Local Roofing/Construction company business needs new biz card design

We need a new business card design, current cards are from the start of this operation and generic at best. We are a local Construction Company (General Contractor) with a majority of our work originating from insurance claims-exterior finish work is the main focus (Roofs-Siding-Gutters etc). Heavily involved with homeowners and the low ball offers they receive from insurance company's after a insurable event takes place. I have attached some of our original logo file(s) below.

```html
<!DOCTYPE html>
<html lang="en">
<head>
<meta charset="utf-8">
<title>Stonefield Construction — Business Card</title>
<link href="https://fonts.googleapis.com/css2?family=Poppins:wght@400;500;600;700&display=swap" rel="stylesheet">
<style>
  :root {
    --backdrop: #1c1d1e;
    --card-ink: #0d1c21;
    --brand-green: #2fd679;
    --paper: #ffffff;
    --text-light: #f2f2f2;
  }
  * { box-sizing: border-box; margin: 0; padding: 0; }
  html, body { width: 1200px; height: 1015px; overflow: hidden; }
  body {
    background: radial-gradient(ellipse at center, #2e2f30 0%, var(--backdrop) 70%, #0e0e0f 100%);
    font-family: "Poppins", sans-serif;
    position: relative;
  }
  .card {
    position: absolute;
    width: 540px;
    height: 309px;
    background: var(--card-ink);
    border-radius: 4px;
    overflow: hidden;
    box-shadow: 0 18px 40px rgba(0,0,0,.55);
  }
  /* Front */
  .card-front { left: 90px; top: 130px; }
  .front-frame {
    position: absolute;
    left: 60px; top: 100px;
    width: 420px; height: 110px;
    border: 2px solid rgba(255,255,255,.12);
    border-radius: 18px;
    display: flex;
    align-items: center;
    gap: 18px;
    padding: 0 28px;
  }
  .brand-square {
    width: 58px; height: 58px;
    background: var(--brand-green);
    flex: none;
  }
  .brand-name {
    color: var(--text-light);
    font-weight: 700;
    font-size: 27px;
    line-height: 1.05;
    letter-spacing: 1px;
    text-transform: uppercase;
  }
  /* Back */
  .card-back { left: 570px; top: 570px; }
  .back-arc { position: absolute; inset: 0; }
  .holder {
    position: absolute;
    left: 40px; top: 70px;
  }
  .holder-name {
    color: var(--brand-green);
    font-weight: 600;
    font-size: 22px;
    letter-spacing: 1px;
    text-transform: uppercase;
    line-height: 1.1;
  }
  .holder-role {
    color: var(--text-light);
    font-size: 15px;
    margin-top: 2px;
  }
  .address {
    position: absolute;
    left: 40px; top: 170px;
    color: var(--text-light);
    font-size: 14px;
    line-height: 1.3;
  }
  .contacts {
    position: absolute;
    left: 40px; top: 222px;
    list-style: none;
    color: var(--text-light);
    font-size: 14px;
    line-height: 1.4;
  }
  .contacts li { display: flex; align-items: center; gap: 7px; }
  .contacts svg { width: 14px; height: 14px; flex: none; }
  .back-brand {
    position: absolute;
    left: 290px; top: 78px;
    width: 230px;
    display: flex;
    flex-direction: column;
    align-items: center;
    gap: 12px;
  }
  .back-brand-square {
    width: 64px; height: 64px;
    background: var(--brand-green);
  }
  .back-brand-name {
    color: var(--brand-green);
    font-weight: 700;
    font-size: 22px;
    line-height: 1.1;
    letter-spacing: 1px;
    text-transform: uppercase;
    text-align: center;
  }
</style>
</head>
<body>

  <section class="card card-front" aria-label="Card front">
    <div class="front-frame">
      <span class="brand-square" aria-hidden="true"></span>
      <p class="brand-name">Stonefield<br>Construction</p>
    </div>
  </section>

  <section class="card card-back" aria-label="Card back">
    <svg class="back-arc" viewBox="0 0 540 309" aria-hidden="true">
      <circle cx="425" cy="130" r="200" fill="var(--brand-green)"/>
      <circle cx="432" cy="124" r="198" fill="var(--paper)"/>
    </svg>

    <div class="holder">
      <p class="holder-name">Daniel Carter</p>
      <p class="holder-role">Managing Director</p>
    </div>

    <p class="address">18 Quarry Lane<br>Millbrook, 45120</p>

    <ul class="contacts">
      <li>
        <svg viewBox="0 0 24 24" aria-hidden="true"><path fill="var(--brand-green)" d="M6.6 10.8a15.1 15.1 0 0 0 6.6 6.6l2.2-2.2c.3-.3.7-.4 1-.2 1.1.4 2.3.6 3.6.6.6 0 1 .4 1 1V20c0 .6-.4 1-1 1A17 17 0 0 1 3 4c0-.6.4-1 1-1h3.5c.6 0 1 .4 1 1 0 1.3.2 2.5.6 3.6.1.3 0 .7-.2 1z"/></svg>
        044-870 215 634
      </li>
      <li>
        <svg viewBox="0 0 24 24" aria-hidden="true"><path fill="var(--brand-green)" d="M2 5h20v14H2zm2 2v.5l8 5 8-5V7l-8 5z"/></svg>
        info@stonefieldbuild.com
      </li>
      <li>
        <svg viewBox="0 0 24 24" aria-hidden="true"><circle cx="12" cy="12" r="9" fill="none" stroke="var(--brand-green)" stroke-width="2"/><path d="M3 12h18M12 3c3 3 3 15 0 18M12 3c-3 3-3 15 0 18" fill="none" stroke="var(--brand-green)" stroke-width="1.6"/></svg>
        www.stonefieldbuild.com
      </li>
    </ul>

    <div class="back-brand">
      <span class="back-brand-square" aria-hidden="true"></span>
      <p class="back-brand-name">Stonefield<br>Construction</p>
    </div>
  </section>

</body>
</html>
```